brqnal new business card design project

we need a new business card design. you can view info about us @ brqnal-example.com. i have attached an example of our previous card with our previous name that we no longer use. We really liked the design, colors etc. look below to see more info about this project. it asks for a limited number of words. please see our website for more info about our compnay.

Target Market(s)

law enforcement

Contact Information for Business Card

i have uploaded an example of what we used before that we liked.

Font styles to use
Serif

```html
<!DOCTYPE html>
<html lang="en">
<head>
<meta charset="utf-8">
<title>Brqnal business card</title>
<link rel="stylesheet" href="https://fonts.googleapis.com/css2?family=Lato:wght@300;400;700;900&display=swap">
<style>
  :root {
    --backdrop: #3b3b3d;
    --navy-deep: #0b1d29;
    --navy-mid: #12303d;
    --teal-glow: #1d4a55;
    --ink: #14222c;
    --ink-soft: #3d4a52;
    --paper: #ffffff;
    --text-light: #ffffff;
  }
  * { box-sizing: border-box; margin: 0; padding: 0; }
  html, body {
    width: 1200px; height: 1200px; overflow: hidden;
    background: var(--backdrop);
    font-family: "Lato", Arial, sans-serif;
  }
  .sheet {
    position: relative; width: 1200px; height: 1200px;
  }
  .card {
    position: absolute; left: 250px; width: 700px; height: 400px;
    box-shadow: 0 10px 30px rgba(0,0,0,0.35);
    overflow: hidden;
  }
  /* Front */
  .card-front {
    top: 150px;
    border-radius: 90px 0 90px 0;
    background: var(--navy-deep);
  }
  .network-texture {
    position: absolute; inset: 0;
    background:
      radial-gradient(ellipse at 45% 85%, var(--teal-glow) 0%, rgba(29,74,85,0) 55%),
      linear-gradient(135deg, var(--navy-mid) 0%, var(--navy-deep) 70%);
  }
  .front-brand {
    position: absolute; left: 0; right: 0; top: 140px;
    text-align: center; color: var(--text-light);
  }
  .front-brand .wordmark {
    font-size: 62px; font-weight: 400; letter-spacing: 8px;
  }
  .front-brand .tagline {
    margin-top: 14px; font-size: 19px; font-weight: 700; letter-spacing: 1px;
  }
  /* Back */
  .card-back {
    top: 650px;
    border-radius: 0 90px 0 90px;
    background: var(--paper);
    color: var(--ink);
  }
  .holder {
    position: absolute; left: 42px; top: 40px;
  }
  .holder .name {
    font-size: 22px; font-weight: 900; letter-spacing: 0.5px;
  }
  .holder .role {
    font-size: 18px; font-weight: 400; color: var(--ink-soft); margin-top: 2px;
  }
  .back-wordmark {
    position: absolute; right: 50px; top: 60px;
    font-size: 56px; font-weight: 400; letter-spacing: 7px; color: var(--ink);
  }
  .contact-list {
    position: absolute; left: 42px; bottom: 60px;
    list-style: none; font-size: 19px; color: var(--ink-soft);
  }
  .contact-list li {
    display: flex; align-items: center; gap: 8px; line-height: 28px;
  }
  .contact-list svg { width: 15px; height: 15px; fill: var(--ink); flex: none; }
  .address {
    position: absolute; right: 50px; bottom: 45px;
    text-align: right; font-size: 19px; line-height: 26px; color: var(--ink-soft);
  }
</style>
</head>
<body>
<main class="sheet">
  <section class="card card-front">
    <div class="network-texture" role="img" aria-label="Faint connected-node network texture in dark teal"></div>
    <div class="front-brand">
      <div class="wordmark">BRQNAL</div>
      <div class="tagline">LAW ENFORCEMENT INNOVATION</div>
    </div>
  </section>

  <section class="card card-back">
    <div class="holder">
      <div class="name">MARCUS REED</div>
      <div class="role">Managing Director</div>
    </div>
    <div class="back-wordmark">BRQNAL</div>
    <ul class="contact-list">
      <li>
        <svg viewBox="0 0 16 16" aria-hidden="true"><path d="M3 1.5h3l1.2 3.2-1.8 1.2a8.5 8.5 0 0 0 4.7 4.7l1.2-1.8 3.2 1.2v3a1.5 1.5 0 0 1-1.5 1.5A12.5 12.5 0 0 1 1.5 3 1.5 1.5 0 0 1 3 1.5z"/></svg>
        866.555.0142
      </li>
      <li>
        <svg viewBox="0 0 16 16" aria-hidden="true"><path d="M1 3h14v10H1zM2 4.2v.3l6 4 6-4v-.3z"/></svg>
        info@brqnal-example.com
      </li>
      <li>
        <svg viewBox="0 0 16 16" aria-hidden="true"><circle cx="8" cy="8" r="7"/></svg>
        www.brqnal-example.com
      </li>
    </ul>
    <address class="address" style="font-style:normal">
      4120 Linden Court<br>Dallas, TX 75201
    </address>
  </section>
</main>
</body>
</html>
```